Client Fulfillment Flyer

This is a document used for internal purposes ie it is not distributed to clients. We would like it to have some colour, images etc. We are in the financial services industry, Ballarat, Victoria, Australia. www.torvenfield.com.au and www.torvenfieldagri.com.au

Target Market(s)

Internal training document

Industry/Entity Type

Finance And Accounting

Colors
3176b5

```html
<!DOCTYPE html>
<html lang="en">
<head>
<meta charset="utf-8">
<title>Torvenfield &amp; Co – Client Fulfillment</title>
<link href="https://fonts.googleapis.com/css2?family=Source+Sans+3:wght@400;600&family=Zilla+Slab:wght@600&display=swap" rel="stylesheet">
<style>
  :root{
    --brand:#1b62dd;
    --ink:#4b5058;
    --rule:#dfe2e6;
    --paper:#ffffff;
    --edge:#2b2b2b;
  }
  html,body{margin:0;padding:0;overflow:hidden;background:var(--paper);}
  .page{
    position:relative;width:939px;height:1200px;overflow:hidden;background:var(--paper);
    font-family:"Source Sans 3",sans-serif;color:var(--ink);
  }
  .page-edge{position:absolute;right:0;top:0;width:1px;height:1198px;background:var(--edge);}
  .page-edge.bottom{right:0;top:auto;bottom:0;width:939px;height:1px;}
  .masthead{position:absolute;left:77px;top:60px;width:793px;height:32px;display:flex;align-items:center;}
  .masthead-dot{width:32px;height:32px;border-radius:50%;background:var(--brand);flex:none;}
  .masthead-name{
    margin-left:6px;font-family:"Source Sans 3",sans-serif;font-weight:600;font-size:19px;
    letter-spacing:.8px;color:var(--brand);text-transform:uppercase;white-space:nowrap;
  }
  .masthead-rule{flex:1;height:1px;background:var(--rule);margin-left:14px;}
  .content{position:absolute;left:142px;top:148px;width:656px;}
  .content p{margin:0 0 14.4px;font-size:13.8px;line-height:20px;text-align:justify;letter-spacing:.15px;}
  .content h2{margin:22px 0 16px;font-weight:400;font-size:17px;line-height:20px;color:var(--brand);letter-spacing:.2px;}
  .folio{position:absolute;left:77px;top:1125px;width:793px;height:1px;background:var(--rule);}
  .folio-badge{
    position:absolute;left:446px;top:1102px;width:44px;height:44px;border-radius:50%;
    background:var(--paper);box-shadow:0 0 0 1px var(--rule);
  }
  .folio-number{
    position:absolute;left:453px;top:1109px;width:30px;height:30px;border-radius:50%;
    background:var(--brand);color:#fff;font-size:16px;line-height:30px;text-align:center;
  }
</style>
</head>
<body>
<div class="page">
  <header class="masthead">
    <span class="masthead-dot"></span>
    <span class="masthead-name">Torvenfield &amp; Co</span>
    <span class="masthead-rule"></span>
  </header>

  <main class="content">
    <p>Our goal by 30th June 2023 is to be helping at least 5,000 client/family groups along their journey to reach the financial goals and dreams they are committed to achieving.</p>

    <h2>How are we going to achieve our Vision?</h2>
    <p>We need to work in an effective and efficient manner to achieve this vision.</p>
    <p>We break the vision down into smaller plans and action items. We then prioritise these steps with responsibility and accountability around each step to be completed.</p>
    <p>As each step is in progress and being completed we are getting closer to achieving our vision. For example the implementation of Ledgerly, Manila and client allocations are all important steps towards achieving our vision.</p>
    <p>We also have a clearly defined Core Purpose, Core Values, and Why – Why we do what we do.</p>
    <p>Our core purpose states the reason we exist. The core values are our fundamental beliefs of how we go about our work on a daily basis. Our Core Purpose and Values stay the same irrespective of how our business changes.</p>
    <p>Understanding our Why helps to provide a connection with our vision and purpose. Rather than focusing on what we do and how we do it, we need to understand why we do it.</p>
    <p>If you understand WHY, it gives a greater purpose to the work you do every day. It’s a mindset – are you at work to process transactions and lodge tax returns or are you here completing an important step in identifying ways to help committed clients achieve financial security?</p>
    <p>The latter mindset will not only ensure you are doing what is required but more importantly help you personally find fulfilment in your role.</p>
    <p>We have Service Standards and Culture Standards. These are the basic rules and expectations of how all team members work and interact.</p>

    <h2>Client Management and Communication</h2>
    <p>Client Management and Communication in the context of delivering Client Fulfillment is understanding our client needs, requirements and expectations and ensuring the delivery is in a manner consistent with our Core Purpose and Core Values whilst achieving our Vision.</p>
    <p>This means to deliver Client Fulfillment and achieve our vision we must plan, organise and execute in a consistent manner so there is a reliable and consistent outcome for our clients.</p>
    <p>People like to feel valued and not just a small part of a big business. Utilising our CRM and technology means that we can reach out to individuals with relevant information to help forge and maintain relationships.</p>
    <p>Having the right people doing the right work as well as following the required systems and processes will ensure there is adequate time to invest in Client Management and Communication.</p>
  </main>

  <footer>
    <div class="folio"></div>
    <div class="folio-badge"></div>
    <div class="folio-number">3</div>
  </footer>

  <div class="page-edge"></div>
  <div class="page-edge bottom"></div>
</div>
</body>
</html>
```